Design a compelling Tarnwove Business Card that will drive people to my site

I want a business card that I can give to people—less to tell them who I am and more to direct them to my website. My website is a portal for Pelmor Aquatics Officials and a place for people who want to become Pelmor Aquatics Officials.
I am uploading my official company logo as well as a business card mockup that I did on my own. Please feel free to completely stray from this design.
I've included a screen recording of the homepage of my website as well.
Target Market(s)
Pelmor Aquatics Officials and people who desire to become one
Contact Information for Business Card
website url
Look and feel
Each slider illustrates characteristics of the customer's brand and the style your logo design should communicate.

```html
<!DOCTYPE html>
<html lang="en">
<head>
<meta charset="utf-8">
<title>Tarnwove Business Card</title>
<link rel="stylesheet" href="https://fonts.googleapis.com/css2?family=Roboto:wght@400;500;700&display=swap">
<style>
  :root {
    --page-bg: #e9eaee;
    --navy-deep: #0b1450;
    --navy-glow: #2e45a0;
    --panel-blue: #324f9f;
    --panel-edge: #2a4490;
    --brand-blue: #2f4fb0;
    --ink: #3a3d46;
    --paper: #ffffff;
    --paper-shade: #f1f2f5;
    --soft-white: #dfe4f3;
  }
  * { box-sizing: border-box; margin: 0; padding: 0; }
  html, body {
    width: 1200px; height: 900px; overflow: hidden;
    background: var(--page-bg);
    font-family: "Roboto", Arial, sans-serif;
  }
  .sheet {
    width: 1200px; height: 900px;
    display: flex; flex-direction: column;
    align-items: center; justify-content: center;
    gap: 60px;
  }
  .card {
    width: 630px; height: 360px;
    position: relative; overflow: hidden;
    box-shadow: 0 8px 22px rgba(20, 25, 60, 0.22);
  }

  /* Back of card */
  .card-back {
    background: radial-gradient(ellipse 60% 65% at 50% 42%, var(--navy-glow) 0%, #1a2a78 45%, var(--navy-deep) 100%);
    display: flex; flex-direction: column; align-items: center;
  }
  .card-back .brand-name {
    margin-top: 118px;
    display: flex; align-items: center; gap: 12px;
    color: var(--soft-white);
    font-weight: 500; font-size: 34px; letter-spacing: 0.5px;
  }
  .brand-dot {
    width: 14px; height: 14px; border-radius: 50%;
    background: var(--soft-white);
  }
  .card-back .divider {
    margin-top: 30px; width: 440px; height: 1px;
    background: linear-gradient(90deg, transparent, rgba(200,210,245,0.7), transparent);
  }
  .card-back .site-url {
    margin-top: 22px;
    color: var(--soft-white);
    font-size: 15px; font-weight: 500; letter-spacing: 9px;
  }

  /* Front of card */
  .card-front { display: flex; background: var(--paper); }
  .front-panel {
    width: 290px; height: 100%;
    background: linear-gradient(160deg, #3856a6 0%, var(--panel-blue) 70%);
    border-right: 12px solid var(--panel-edge);
    display: flex; align-items: flex-end; justify-content: center;
    padding-bottom: 86px;
  }
  .front-panel .brand-name {
    display: flex; align-items: center; gap: 10px;
    color: var(--paper);
    font-weight: 500; font-size: 46px; letter-spacing: -0.5px;
  }
  .front-panel .brand-dot { width: 16px; height: 16px; background: var(--paper); }
  .front-details {
    flex: 1;
    background: linear-gradient(120deg, var(--paper-shade) 0%, var(--paper) 55%);
    padding: 96px 0 0 52px;
  }
  .person-name { color: var(--brand-blue); font-weight: 700; font-size: 22px; }
  .person-role { color: var(--ink); font-size: 17px; margin-top: 3px; }
  .name-rule { width: 46px; height: 2px; background: var(--brand-blue); margin: 10px 0 20px; }
  .contact-list { list-style: none; }
  .contact-list li {
    display: flex; align-items: center; gap: 10px;
    color: var(--ink); font-size: 17px; margin-bottom: 9px;
  }
  .contact-list svg { width: 16px; height: 16px; fill: var(--brand-blue); flex: none; }
</style>
</head>
<body>
  <main class="sheet">
    <section class="card card-back" aria-label="Card back">
      <div class="brand-name"><span class="brand-dot"></span>tarnwove</div>
      <div class="divider"></div>
      <p class="site-url">www.tarnwove.com</p>
    </section>

    <section class="card card-front" aria-label="Card front">
      <div class="front-panel">
        <div class="brand-name"><span class="brand-dot"></span>tarnwove</div>
      </div>
      <div class="front-details">
        <h1 class="person-name">Martin Halvey</h1>
        <p class="person-role">CEO &amp; Founder</p>
        <div class="name-rule"></div>
        <ul class="contact-list">
          <li>
            <svg viewBox="0 0 24 24" aria-hidden="true"><path d="M6.6 10.8a15.1 15.1 0 0 0 6.6 6.6l2.2-2.2a1 1 0 0 1 1-.25 11.4 11.4 0 0 0 3.6.57 1 1 0 0 1 1 1V20a1 1 0 0 1-1 1A17 17 0 0 1 3 4a1 1 0 0 1 1-1h3.5a1 1 0 0 1 1 1c0 1.25.2 2.45.57 3.57a1 1 0 0 1-.25 1z"/></svg>
            (555) 201-4837
          </li>
          <li>
            <svg viewBox="0 0 24 24" aria-hidden="true"><path d="M2 5h20v14H2z" fill="none"/><path d="M2 5h20v14H2V5zm2 2v.5l8 5.5 8-5.5V7H4zm0 2.9V17h16V9.9l-8 5.5-8-5.5z"/></svg>
            martin@tarnwove.com
          </li>
        </ul>
      </div>
    </section>
  </main>
</body>
</html>
```